New Business Card Design for Manufacturing

We are an engineering/manufacturing company that offers Advanced machining/assembly/engineering services, as well as innovative products for the heavy duty engine cooling markets.

We are looking to get a new business card designed that is clean and modern looking, but still fits the wide range of technical/skilled work we do.

- We hope to use this design as the base for other design work in new Presentations, web, and print work.

Industry/Entity Type

Engineering

Contact Information for Business Card

Our preferred color of blue is (RGB) 22/71/159 but can vary slightly from that color. Our content will be our Logo and full company name (Vantrell Forge Works, Inc.), company address, name, job title, phone number with extension, cell number, fax number, website, and email address on the cards.
We'd like the full company name next to the logo, but we are open to other interpretations of that layout.
Preferably, we would like the back side to be clean with just our logo, and the front to contain all of the contact information.

Colors
2f74b4
0355a3
85abd2

Requirements
Must have
• - Logo, company name, needed content - We are open to interpretation beyond that.
• - Standard size business card.
• - Horizontal orientation.
• - Enough space for lengthy names / job titles (for example, a job title could read "Directory of Human Resources" or "V.P. of Governmental Affairs"). We need this to look clean, whether the title be short (CEO) or long (as described above).

```html
<!DOCTYPE html>
<html lang="en">
<head>
<meta charset="utf-8">
<title>Vantrell Forge Works – Business Card</title>
<link href="https://fonts.googleapis.com/css2?family=Roboto:wght@400;500;700&display=swap" rel="stylesheet">
<style>
  :root {
    --brand-blue: #0d56a6;
    --back-blue: #1452a4;
    --back-mark: #0e3f85;
    --ink-gray: #5f6166;
    --rule-gray: #8c8e92;
    --band-gray: #868b91;
    --paper: #ffffff;
    --stage: #e4e5e7;
  }
  * { margin: 0; padding: 0; box-sizing: border-box; }
  html, body { width: 1200px; height: 960px; overflow: hidden; }
  body {
    background: var(--stage);
    position: relative;
    font-family: "Roboto", Arial, sans-serif;
  }
  .card {
    position: absolute;
    left: 278px;
    width: 641px;
    height: 366px;
    box-shadow: 0 4px 10px rgba(0,0,0,0.25);
    overflow: hidden;
  }
  .card-front { top: 88px; background: var(--paper); }
  .card-back { top: 510px; background: var(--back-blue); }

  .brand {
    position: absolute;
    left: 44px;
    top: 50px;
    display: flex;
    align-items: center;
    gap: 10px;
  }
  .brand-square { width: 26px; height: 26px; background: var(--brand-blue); }
  .brand-name {
    font-weight: 700;
    font-size: 22px;
    color: var(--brand-blue);
    letter-spacing: 0.2px;
  }

  .person {
    position: absolute;
    right: 46px;
    top: 176px;
    text-align: right;
  }
  .person-name { font-size: 25px; font-weight: 500; color: var(--brand-blue); line-height: 1.1; }
  .person-title { font-size: 15px; color: var(--ink-gray); margin-top: 6px; }
  .edge-tab {
    position: absolute;
    right: 0; top: 177px;
    width: 17px; height: 58px;
    background: var(--brand-blue);
  }
  .divider {
    position: absolute;
    left: 43px; top: 239px;
    width: 553px; height: 1px;
    background: var(--rule-gray);
  }

  .contact-list {
    position: absolute;
    left: 43px; top: 250px;
    list-style: none;
  }
  .contact-list li {
    display: flex; align-items: center; gap: 7px;
    font-size: 15px; color: var(--ink-gray);
    height: 20.7px;
  }
  .contact-list svg { width: 13px; height: 13px; fill: var(--brand-blue); flex: none; }

  .address {
    position: absolute;
    right: 40px; top: 292px;
    text-align: right;
    font-size: 15px; color: var(--ink-gray);
    line-height: 20.7px;
  }

  .footer-bands { position: absolute; left: 0; bottom: 0; width: 641px; height: 28px; }
  .web-address {
    position: absolute;
    right: 38px; bottom: 5px;
    font-size: 15px; font-weight: 500; color: #ffffff;
  }

  .back-brand {
    position: absolute;
    left: 0; right: 0; top: 165px;
    display: flex; justify-content: center; align-items: center; gap: 12px;
  }
  .back-brand .brand-square { width: 34px; height: 34px; background: var(--back-mark); }
  .back-brand .brand-name { font-size: 30px; color: var(--back-mark); }
</style>
</head>
<body>
  <section class="card card-front" aria-label="Business card front">
    <div class="brand">
      <span class="brand-square"></span>
      <span class="brand-name">Vantrell Forge Works, Inc.</span>
    </div>

    <div class="person">
      <div class="person-name">Dana Whitlock</div>
      <div class="person-title">General Manager</div>
    </div>
    <div class="edge-tab"></div>
    <div class="divider"></div>

    <ul class="contact-list">
      <li>
        <svg viewBox="0 0 16 16" aria-hidden="true"><path d="M3.6 1.2l2.3 2.6-1.3 2a9 9 0 005.6 5.6l2-1.3 2.6 2.3-1.5 2.2C7 14.4 1.6 9 1.4 2.7z"/></svg>
        000-0000-0000
      </li>
      <li>
        <svg viewBox="0 0 16 16" aria-hidden="true"><path d="M4.5 0.5h7a1 1 0 011 1v13a1 1 0 01-1 1h-7a1 1 0 01-1-1v-13a1 1 0 011-1zm0.6 2v9.5h5.8V2.5zM8 12.8a0.9 0.9 0 100 1.8 0.9 0.9 0 000-1.8z"/></svg>
        000-0000-0000
      </li>
      <li>
        <svg viewBox="0 0 16 16" aria-hidden="true"><path d="M4 1h8v4H4zM1.5 6h13a1 1 0 011 1v5h-3V9.5h-9V12h-3V7a1 1 0 011-1zM4.5 10.5h7V15h-7z"/></svg>
        000-0000-0000
      </li>
      <li>
        <svg viewBox="0 0 16 16" aria-hidden="true"><path d="M1 3h14v1.2L8 9 1 4.2zM1 5.8l7 4.8 7-4.8V13H1z"/></svg>
        info@vantrellforge.com
      </li>
    </ul>

    <div class="address">2480 N. 14th Street,<br>Marquette, MI 49855</div>

    <svg class="footer-bands" viewBox="0 0 641 28" aria-hidden="true">
      <polygon points="0,15 438,15 429,28 0,28" fill="var(--band-gray)"/>
      <polygon points="441,2 641,2 641,28 425,28" fill="var(--brand-blue)"/>
    </svg>
    <div class="web-address">www.vantrellforge.com</div>
  </section>

  <section class="card card-back" aria-label="Business card back">
    <div class="back-brand">
      <span class="brand-square"></span>
      <span class="brand-name">Vantrell Forge Works, Inc.</span>
    </div>
  </section>
</body>
</html>
```